Business Card for Vorla Parts Wholesale supplier

Hi There! I need a new business card for our company. We are specialized in selling Vorla parts, mostly we sell new LCD screens for Zelnar and Drelks. I would like to see that back in the design.

You can find the colors and logo's on our website: www.hartuvo.nl

Industry/Entity Type

Business

Contact Information for Business Card

My Details:
Tobias Lindqvist

Phone: 0031687203316
E-mail: Tobias@hartuvo.nl

Slogan: "Built For Every Repair"

Font styles to use
Sans Serif

Colors

Designer to choose colors to be used in the design.

Requirements
Must have
• A Black backside with the Hartuvo logo on it. The front side should be clean with only my contact details.
• But I'm also open for something really different or awesome!
Nice to have
• Remember that we are in the parts & repairing industry, So i'll be handing those business cards mainly to repair companies. Maybe you can do something with that thought :)

```html
<!DOCTYPE html>
<html lang="en">
<head>
<meta charset="utf-8">
<title>Hartuvo Business Card</title>
<link href="https://fonts.googleapis.com/css2?family=Exo+2:wght@400;700&family=PT+Sans:wght@700&display=swap" rel="stylesheet">
<style>
  :root {
    --orange: #f47321;
    --black: #000000;
    --white: #ffffff;
    --ink: #111111;
    --backdrop: #e6e2dc;
  }
  html, body {
    margin: 0;
    padding: 0;
    width: 1200px;
    height: 987px;
    overflow: hidden;
    background: var(--backdrop);
  }
  .canvas {
    position: relative;
    width: 1200px;
    height: 987px;
  }
  .card {
    position: absolute;
    left: 293px;
    width: 615px;
    height: 350px;
    overflow: hidden;
    box-shadow: 0 3px 10px rgba(0,0,0,0.25);
  }
  .card-front { top: 130px; background: var(--white); }
  .card-back { top: 506px; background: var(--black); }

  .front-shapes { position: absolute; inset: 0; }

  .brand {
    position: absolute;
    left: 47px;
    top: 56px;
    display: flex;
    align-items: center;
    gap: 12px;
  }
  .brand-square {
    width: 40px;
    height: 40px;
    background: var(--orange);
  }
  .brand-name {
    font-family: "Exo 2", sans-serif;
    font-weight: 700;
    font-size: 46px;
    line-height: 1;
    color: var(--ink);
    letter-spacing: 0.5px;
  }

  .holder-name {
    position: absolute;
    left: 47px;
    top: 273px;
    margin: 0;
    font-family: "Exo 2", sans-serif;
    font-weight: 700;
    font-size: 23px;
    color: var(--orange);
    letter-spacing: 0.3px;
  }

  .contact-list {
    position: absolute;
    left: 396px;
    top: 246px;
    margin: 0;
    padding: 0;
    list-style: none;
    font-family: "Exo 2", sans-serif;
    font-size: 16px;
    color: var(--white);
  }
  .contact-list li {
    display: flex;
    align-items: center;
    gap: 8px;
    height: 24px;
  }
  .contact-icon { width: 15px; height: 15px; flex: none; }

  .back-brand {
    position: absolute;
    left: 0;
    right: 0;
    top: 118px;
    display: flex;
    justify-content: center;
    align-items: center;
    gap: 14px;
  }
  .back-brand .brand-square { width: 46px; height: 46px; }
  .back-brand .brand-name { color: var(--orange); font-size: 56px; }

  .slogan {
    position: absolute;
    left: 0;
    right: 0;
    top: 278px;
    margin: 0;
    text-align: center;
    font-family: "PT Sans", sans-serif;
    font-weight: 700;
    font-size: 20px;
    color: var(--white);
  }
</style>
</head>
<body>
<div class="canvas">

  <section class="card card-front">
    <svg class="front-shapes" width="615" height="350" viewBox="0 0 615 350">
      <polygon points="0,217 321,217 311,229 0,229" fill="var(--orange)"/>
      <polygon points="0,232 313,232 342,196 615,196 615,350 0,350" fill="var(--black)"/>
    </svg>

    <div class="brand">
      <span class="brand-square"></span>
      <span class="brand-name">hartuvo</span>
    </div>

    <h1 class="holder-name">Tobias Lindqvist</h1>

    <ul class="contact-list">
      <li>
        <svg class="contact-icon" viewBox="0 0 16 16"><path fill="var(--orange)" d="M3.6 1.2l2.3 2.6-1.3 2a9 9 0 0 0 5.6 5.6l2-1.3 2.6 2.3-1.5 2.4C7.2 14.6 1.4 8.8 1.2 2.7z"/></svg>
        0031687203316
      </li>
      <li>
        <svg class="contact-icon" viewBox="0 0 16 16"><rect x="1" y="3" width="14" height="10" fill="var(--orange)"/><polyline points="1,3 8,9 15,3" fill="none" stroke="var(--black)" stroke-width="1.3"/></svg>
        Tobias@hartuvo.nl
      </li>
      <li>
        <svg class="contact-icon" viewBox="0 0 16 16"><circle cx="8" cy="8" r="7" fill="var(--orange)"/><path d="M5 4c2 1 1 3 3 3s1 3 -1 4M10 3c-1 2 1 2 3 3" fill="none" stroke="var(--black)" stroke-width="1.2"/></svg>
        www.hartuvo.nl
      </li>
    </ul>
  </section>

  <section class="card card-back">
    <div class="back-brand">
      <span class="brand-square"></span>
      <span class="brand-name">hartuvo</span>
    </div>
    <p class="slogan">Built For Every Repair</p>
  </section>

</div>
</body>
</html>
```